Real Estate Webpage Design

We have an existing website: ferndaleestatecollective.com.au
We focus customised service mainly on Property Management and second-hand property sales.
We are not entirely happy about the current design and layout can stay roughly the same as the back end coding is linked to a CRM system.
We would like to see the design are more reachable to our clients and appearing.
Please check our Website Design Draft for more details.

Industry/Entity Type

Real estate Agency

Number of Pages Required

5+ page

Font styles to use
Sans Serif

Colors

Designer to choose colors to be used in the design.

```html
<!DOCTYPE html>
<html lang="en">
<head>
<meta charset="utf-8">
<title>Property Sales – Ferndale Estate</title>
<link href="https://fonts.googleapis.com/css2?family=Montserrat:wght@400;500&family=Roboto:wght@400;500;700&display=swap" rel="stylesheet">
<style>
:root{
  --gold:#f8b317;
  --ink:#1e1e1e;
  --muted:#8a8a8a;
  --line:#e6e6e6;
  --cream:#fdf8ec;
  --band:#f7f7f7;
  --badge:#24313d;
}
*{box-sizing:border-box;margin:0;padding:0}
html,body{width:1200px;height:4335px;overflow:hidden}
body{position:relative;font-family:"Montserrat",sans-serif;color:var(--ink);background:#fff}
.abs{position:absolute}
.center{text-align:center;left:0;width:1200px}
h2.section-title{font-family:"Roboto",sans-serif;font-weight:500;font-size:33px;color:var(--ink)}

/* header */
.site-header{left:0;top:0;width:1200px;height:59px;background:#fff;z-index:3}
.brand{left:61px;top:0;width:224px;height:74px;background:#fff;z-index:4;display:flex;align-items:center;gap:10px;padding-left:16px}
.brand-mark{width:26px;height:26px;background:var(--gold)}
.brand-name{font-family:"Roboto",sans-serif;font-weight:700;font-size:25px;color:var(--gold)}
.main-nav{left:325px;top:22px;display:flex;gap:28px;font-family:"Roboto",sans-serif;font-size:14px;z-index:4}
.main-nav a{color:#333;text-decoration:none;padding-bottom:13px}
.main-nav a.active{color:var(--gold);border-bottom:2px solid var(--gold)}
.btn-add{left:1011px;top:17px;width:128px;height:35px;background:var(--gold);color:#fff;font-family:"Roboto",sans-serif;font-size:13px;display:flex;align-items:center;justify-content:center;border:2px solid #e3a000;z-index:4}

/* hero */
.hero{left:0;top:59px;width:1200px;height:350px;background:linear-gradient(180deg,#5f6f6a 0%,#3c4a3e 45%,#22301f 100%)}
.hero-title{left:61px;top:196px;font-family:"Roboto",sans-serif;font-weight:700;font-size:37px;color:var(--gold)}
.hero-sub{left:61px;top:252px;font-size:13px;color:#fff}

/* intro */
.intro{left:61px;top:390px;width:1078px;height:329px;background:var(--cream);text-align:center}
.intro h2{margin-top:52px}
.intro p{width:650px;margin:18px auto 0;font-size:13px;line-height:22.5px;color:var(--muted)}
.intro p + p{margin-top:12px}

/* testimonial */
.testi-title{top:797px;font-family:"Roboto",sans-serif;font-weight:500;font-size:33px}
.quote-mark{left:598px;top:855px}
.testi-text{left:366px;top:902px;width:504px;text-align:center;font-size:13px;line-height:22.5px;color:var(--muted)}
.arrow{width:37px;height:37px;display:flex;align-items:center;justify-content:center}
.arrow.prev{left:217px;top:961px;background:var(--gold)}
.arrow.next{left:944px;top:961px;border:1px solid var(--gold);background:#fff}
.testi-name{top:1034px;font-size:13px}
.testi-role{top:1058px;font-size:13px;color:var(--gold)}

/* advantage */
.advantage{left:0;top:1155px;width:1200px;height:444px;background:var(--band)}
.advantage h2{position:absolute;top:48px;width:100%;text-align:center}
.adv-item{position:absolute;top:113px;width:250px;text-align:center}
.adv-icon{width:56px;height:56px;margin:0 auto;border-radius:8px;background:linear-gradient(135deg,#fde4a8,#f8b317 60%,#2d3b48)}
.adv-item h3{margin-top:20px;font-family:"Roboto",sans-serif;font-weight:400;font-size:16px}
.adv-item p{margin-top:8px;font-size:12.5px;line-height:22.5px;color:var(--muted)}
.btn-switch{position:absolute;left:550px;top:356px;width:100px;height:34px;background:var(--gold);color:#fff;font-size:12px;display:flex;align-items:center;justify-content:center;border:2px solid #e3a000}

/* listings */
.search{left:61px;width:1075px;height:47px;background:#fff;box-shadow:0 1px 6px rgba(0,0,0,.12);display:flex}
.search .select{width:106px;border-right:1px solid var(--line);display:flex;align-items:center;justify-content:space-between;padding:0 14px;font-size:13px}
.search .field{flex:1;display:flex;align-items:center;padding-left:16px;font-size:13px;color:var(--muted)}
.search .go{width:45px;margin:3px;background:var(--gold);display:flex;align-items:center;justify-content:center}
.more{left:1000px;width:136px;text-align:right;font-size:12px;color:var(--gold)}
.more b{color:var(--ink);font-weight:500;margin-right:14px}
.cards{left:61px;width:1078px;display:grid;grid-template-columns:repeat(3,338px);column-gap:32px;row-gap:25px}
.card{position:relative;height:389px;background:#fff;box-shadow:0 1px 8px rgba(0,0,0,.12)}
.card .photo{position:absolute;left:9px;top:9px;right:9px;height:186px}
.card .badge{position:absolute;left:0;top:0;padding:4px 9px;background:var(--badge);color:#fff;font-size:11.5px}
.card .price{position:absolute;left:25px;top:150px;color:#fff;font-family:"Roboto",sans-serif;font-weight:500;font-size:16px}
.card h3{position:absolute;left:21px;top:208px;font-family:"Roboto",sans-serif;font-weight:500;font-size:17px}
.card .addr{position:absolute;left:21px;top:247px;display:flex;gap:8px;align-items:center;font-size:12.5px}
.card .feats{position:absolute;left:21px;top:285px;display:flex;gap:16px;font-size:12.5px}
.card .feats span{display:flex;align-items:center;gap:6px}
.card .agent{position:absolute;left:0;right:0;top:334px;border-top:1px solid var(--line);height:55px;display:flex;align-items:center;padding:0 19px;font-size:12.5px}
.avatar{width:28px;height:28px;background:linear-gradient(135deg,#c9c3bb,#7d746c);margin-right:12px}
.agent .tools{margin-left:auto;display:flex;gap:10px}
.pager{left:0;width:1200px;display:flex;justify-content:center;gap:15px}
.pager span{width:37px;height:37px;display:flex;align-items:center;justify-content:center;border:1px solid #555;font-size:14px;background:#fff}
.pager .dark{background:#222;border-color:#222}
.pager .on{background:var(--gold);border-color:var(--gold);color:#fff}
.sold-band{left:0;top:2836px;width:1200px;height:1166px;background:var(--band)}

/* footer */
.footer{left:0;top:4002px;width:1200px;height:333px;background:#fff}
.f-brand{left:61px;top:48px;display:flex;align-items:center;gap:10px}
.f-about{left:61px;top:124px;width:210px;font-size:12px;line-height:21px}
.f-col{top:40px}
.f-col h4{font-weight:400;font-size:12px;color:var(--gold);margin-bottom:14px}
.f-col li{list-style:none;font-size:12px;line-height:29.5px;padding-left:5px}
.contact-row{display:flex;gap:14px;font-size:12px;line-height:20px;margin-bottom:10px}
.socials{display:flex;gap:16px}
.socials span{width:36px;height:36px;border-radius:50%;border:2px solid var(--gold)}
.socials span.filled{background:var(--gold)}
.f-bottom{left:61px;top:4303px;width:1078px;border-top:1px solid var(--line);padding-top:8px;display:flex;font-size:11.5px}
.f-bottom nav{margin-left:auto;display:flex;gap:26px}
</style>
</head>
<body>
<svg width="0" height="0" style="position:absolute">
  <defs>
    <symbol id="i-pin" viewBox="0 0 16 16"><path d="M8 1a5 5 0 0 0-5 5c0 4 5 9 5 9s5-5 5-9a5 5 0 0 0-5-5z" fill="none" stroke="#f8b317" stroke-width="1.3"/><circle cx="8" cy="6" r="1.8" fill="none" stroke="#f8b317" stroke-width="1.3"/></symbol>
    <symbol id="i-bed" viewBox="0 0 22 16"><path d="M2 13V3M2 9h18v4M5 9V6h12v3" fill="none" stroke="#f8b317" stroke-width="1.3"/></symbol>
    <symbol id="i-bath" viewBox="0 0 22 16"><path d="M3 8h16v3a3 3 0 0 1-3 3H6a3 3 0 0 1-3-3zM6 8V3h3" fill="none" stroke="#f8b317" stroke-width="1.3"/></symbol>
    <symbol id="i-car" viewBox="0 0 24 16"><path d="M2 11h20v-2l-3-1-3-4H8L5 8 2 9z" fill="none" stroke="#f8b317" stroke-width="1.3"/><circle cx="7" cy="12" r="1.8" fill="#fff" stroke="#f8b317" stroke-width="1.3"/><circle cx="17" cy="12" r="1.8" fill="#fff" stroke="#f8b317" stroke-width="1.3"/></symbol>
    <symbol id="i-clock" viewBox="0 0 16 16"><circle cx="8" cy="8" r="6" fill="none" stroke="#555" stroke-width="1.3"/><path d="M8 4v4l3 2" fill="none" stroke="#555" stroke-width="1.3"/></symbol>
    <symbol id="i-expand" viewBox="0 0 16 16"><path d="M2 6V2h4M10 2h4v4M14 10v4h-4M6 14H2v-4M2 2l4 4M14 2l-4 4M14 14l-4-4M2 14l4-4" fill="none" stroke="#555" stroke-width="1.3"/></symbol>
    <symbol id="i-mail" viewBox="0 0 16 16"><rect x="1.5" y="3.5" width="13" height="9" fill="none" stroke="#555" stroke-width="1.3"/><path d="M1.5 3.5 8 9l6.5-5.5" fill="none" stroke="#555" stroke-width="1.3"/></symbol>
    <symbol id="i-search" viewBox="0 0 20 20"><circle cx="8.5" cy="8.5" r="5.5" fill="none" stroke="#fff" stroke-width="2"/><path d="M13 13l4 4" stroke="#fff" stroke-width="2"/></symbol>
    <symbol id="i-caret" viewBox="0 0 10 6"><path d="M0 0h10L5 6z" fill="#222"/></symbol>
  </defs>
</svg>

<header>
  <div class="abs site-header"></div>
  <div class="abs brand"><span class="brand-mark"></span><span class="brand-name">Ferndale Estate</span></div>
  <nav class="abs main-nav">
    <a href="#">Home</a><a href="#">About Us</a><a href="#">Landload</a><a href="#">Tenant</a><a href="#">Make a Switch</a><a href="#" class="active">Property Sales</a><a href="#">Appraisal now</a>
  </nav>
  <div class="abs btn-add">Add Properties</div>
</header>

<section>
  <div class="abs hero" role="img" aria-label="Modern two-storey home with large glass windows among trees"></div>
  <h1 class="abs hero-title">Property Sales</h1>
  <p class="abs hero-sub">Your local real estate property group</p>
</section>

<section class="abs intro">
  <h2 class="section-title">Property &nbsp;Sales</h2>
  <p>Lorem Ipsum is simply dummy text of the printing and typesetting industry. Lorem Ipsum has been the industry's standard dummy text ever since the 1500s, when an unknown printer took a galley of type and scrambled it to make a type specimen book. It has survived not only five centuries, but also the leap into electronic typesetting, remaining essentially unchanged.</p>
  <p>It was popularised in the 1960s with the release of Letraset sheets containing Lorem Ipsum passages, and more recently with desktop publishing software like Aldus PageMaker including versions of Lorem Ipsum.</p>
</section>

<section>
  <h2 class="abs center testi-title">What our senior property manager says</h2>
  <svg class="abs quote-mark" width="38" height="32" viewBox="0 0 38 32"><path d="M2 30V16C2 8 6 3 14 1l1 4c-5 2-7 5-7 9h7v16zM22 30V16c0-8 4-13 12-15l1 4c-5 2-7 5-7 9h7v16z" fill="#f8b317"/></svg>
  <p class="abs testi-text">Lorem Ipsum is simply dummy text of the printing and typesetting industry. Lorem Ipsum has been the industry's standard dummy text ever since the 1500s, when an unknown printer took a galley of type and scrambled it to make a type specimen book. It has survived not only five centuries, but also the leap into electronic typesetting, remaining essentially unchanged.</p>
  <div class="abs arrow prev"><svg width="10" height="16" viewBox="0 0 10 16"><path d="M8 2 2 8l6 6" fill="none" stroke="#fff" stroke-width="1.8"/></svg></div>
  <div class="abs arrow next"><svg width="10" height="16" viewBox="0 0 10 16"><path d="M2 2l6 6-6 6" fill="none" stroke="#222" stroke-width="1.8"/></svg></div>
  <p class="abs center testi-name">Mei Lin</p>
  <p class="abs center testi-role">Director and Property Manager</p>
</section>

<section class="abs advantage">
  <h2 class="section-title">Our advantage</h2>
  <div class="adv-item" style="left:60px"><div class="adv-icon" role="img" aria-label="House with tools icon"></div><h3>Maintenance</h3><p>Lorem Ipsum is simply dummy text of the printing and typesetting industry. Lorem Ipsum has been the industry's standard dummy text.</p></div>
  <div class="adv-item" style="left:336px"><div class="adv-icon" role="img" aria-label="Hand holding house icon"></div><h3>Resale</h3><p>Lorem Ipsum is simply dummy text of the printing and typesetting industry. Lorem Ipsum has been the industry's standard dummy text.</p></div>
  <div class="adv-item" style="left:605px"><div class="adv-icon" role="img" aria-label="House with door icon"></div><h3>Rental</h3><p>Lorem Ipsum is simply dummy text of the printing and typesetting industry. Lorem Ipsum has been the industry's standard dummy text.</p></div>
  <div class="adv-item" style="left:900px"><div class="adv-icon" role="img" aria-label="House over hand icon"></div><h3>High Quality Services</h3><p>Lorem Ipsum is simply dummy text of the printing and typesetting industry. Lorem Ipsum has been the industry's standard dummy text.</p></div>
  <div class="btn-switch">Switch Now</div>
</section>

<!-- For sale listings -->
<section>
  <h2 class="abs center section-title" style="top:1679px">For Sales</h2>
  <div class="abs search" style="top:1739px">
    <div class="select">Rent <svg width="10" height="6"><use href="#i-caret"/></svg></div>
    <div class="field">Search by Suburb, Postcode or keyword</div>
    <div class="go"><svg width="20" height="20"><use href="#i-search"/></svg></div>
  </div>
  <p class="abs more" style="top:1808px"><b>+</b>View More Options</p>
  <div class="abs cards" style="top:1853px">
    <article class="card"><div class="photo" role="img" aria-label="Bright open living room and kitchen" style="background:linear-gradient(135deg,#ece6dc,#b9ad9c 55%,#6b6256)"></div><span class="badge">On Sale</span><span class="price">$369,900+</span><h3>Ferndale Park</h3><p class="addr"><svg width="14" height="14"><use href="#i-pin"/></svg>35/12 Banksia Drive Elmstone</p><div class="feats"><span><svg width="22" height="16"><use href="#i-bed"/></svg>3</span><span><svg width="22" height="16"><use href="#i-bath"/></svg>2</span><span><svg width="24" height="16"><use href="#i-car"/></svg>2</span></div><div class="agent"><span class="avatar"></span>Mei Lin<span class="tools"><svg width="16" height="16"><use href="#i-clock"/></svg><svg width="16" height="16"><use href="#i-expand"/></svg><svg width="16" height="16"><use href="#i-mail"/></svg></span></div></article>
    <article class="card"><div class="photo" role="img" aria-label="Aerial view of waterfront apartment complex" style="background:linear-gradient(180deg,#a9c7df,#5f8a7a 55%,#2f5f8a)"></div><span class="badge">On Sale</span><span class="price">$369,900+</span><h3>Ferndale Park</h3><p class="addr"><svg width="14" height="14"><use href="#i-pin"/></svg>102/45 Harbour View Lakeside</p><div class="feats"><span><svg width="22" height="16"><use href="#i-bed"/></svg>2</span><span><svg width="22" height="16"><use href="#i-bath"/></svg>2</span><span><svg width="24" height="16"><use href="#i-car"/></svg>2</span></div><div class="agent"><span class="avatar"></span>Mei Lin<span class="tools"><svg width="16" height="16"><use href="#i-clock"/></svg><svg width="16" height="16"><use href="#i-expand"/></svg><svg width="16" height="16"><use href="#i-mail"/></svg></span></div></article>
    <article class="card"><div class="photo" role="img" aria-label="Living room with sofa and large windows" style="background:linear-gradient(135deg,#f1eee9,#cfc6ba 55%,#9a7a5e)"></div><span class="badge">On Sale</span><span class="price">$369,900+</span><h3>Ferndale Park</h3><p class="addr"><svg width="14" height="14"><use href="#i-pin"/></svg>1/3 Maple Place Ashby</p><div class="feats"><span><svg width="22" height="16"><use href="#i-bed"/></svg>3</span><span><svg width="22" height="16"><use href="#i-bath"/></svg>2</span><span><svg width="24" height="16"><use href="#i-car"/></svg>2</span></div><div class="agent"><span class="avatar"></span>Mei Lin<span class="tools"><svg width="16" height="16"><use href="#i-clock"/></svg><svg width="16" height="16"><use href="#i-expand"/></svg><svg width="16" height="16"><use href="#i-mail"/></svg></span></div></article>
    <article class="card"><div class="photo" role="img" aria-label="Aerial view of suburban homes" style="background:linear-gradient(180deg,#c3d0dc,#8c9a8a 50%,#5c7a4a)"></div><span class="badge">On Sale</span><h3>Ferndale Park</h3><p class="addr"><svg width="14" height="14"><use href="#i-pin"/></svg>25 Kestrel Street Hillcrest</p><div class="feats"><span><svg width="22" height="16"><use href="#i-bed"/></svg>5</span><span><svg width="22" height="16"><use href="#i-bath"/></svg>3</span><span><svg width="24" height="16"><use href="#i-car"/></svg>2</span></div><div class="agent"><span class="avatar"></span>Mei Lin<span class="tools"><svg width="16" height="16"><use href="#i-clock"/></svg><svg width="16" height="16"><use href="#i-expand"/></svg><svg width="16" height="16"><use href="#i-mail"/></svg></span></div></article>
    <article class="card"><div class="photo" role="img" aria-label="Two-storey house front with garage at dusk" style="background:linear-gradient(180deg,#c9a9b4,#8b8f99 45%,#3d4a45)"></div><span class="badge">On Sale</span><h3>Ferndale Park</h3><p class="addr"><svg width="14" height="14"><use href="#i-pin"/></svg>364 Riverbend Drive Ferndale Park</p><div class="feats"><span><svg width="22" height="16"><use href="#i-bed"/></svg>4</span><span><svg width="22" height="16"><use href="#i-bath"/></svg>3</span><span><svg width="24" height="16"><use href="#i-car"/></svg>2</span></div><div class="agent"><span class="avatar"></span>Mei Lin<span class="tools"><svg width="16" height="16"><use href="#i-clock"/></svg><svg width="16" height="16"><use href="#i-expand"/></svg><svg width="16" height="16"><use href="#i-mail"/></svg></span></div></article>
    <article class="card"><div class="photo" role="img" aria-label="Brick home with swimming pool" style="background:linear-gradient(180deg,#6fa0d6,#b77a4e 50%,#2a9fc9)"></div><span class="badge">On Sale</span><h3>Ferndale Park</h3><p class="addr"><svg width="14" height="14"><use href="#i-pin"/></svg>39 Cedar Crescent Oakvale</p><div class="feats"><span><svg width="22" height="16"><use href="#i-bed"/></svg>5</span><span><svg width="22" height="16"><use href="#i-bath"/></svg>5</span><span><svg width="24" height="16"><use href="#i-car"/></svg>4</span></div><div class="agent"><span class="avatar"></span>Mei Lin<span class="tools"><svg width="16" height="16"><use href="#i-clock"/></svg><svg width="16" height="16"><use href="#i-expand"/></svg><svg width="16" height="16"><use href="#i-mail"/></svg></span></div></article>
  </div>
  <div class="abs pager" style="top:2715px">
    <span class="dark"><svg width="10" height="14" viewBox="0 0 10 14"><path d="M7 2 2 7l5 5" fill="none" stroke="#fff" stroke-width="1.6"/></svg></span><span>1</span><span class="on">2</span><span>3</span><span class="dark"><svg width="10" height="14" viewBox="0 0 10 14"><path d="M3 2l5 5-5 5" fill="none" stroke="#fff" stroke-width="1.6"/></svg></span>
  </div>
</section>

<!-- Sold listings -->
<section>
  <div class="abs sold-band"></div>
  <h2 class="abs center section-title" style="top:2888px">Sold Property</h2>
  <div class="abs search" style="top:2949px">
    <div class="select">Rent <svg width="10" height="6"><use href="#i-caret"/></svg></div>
    <div class="field">Search by Suburb, Postcode or keyword</div>
    <div class="go"><svg width="20" height="20"><use href="#i-search"/></svg></div>
  </div>
  <p class="abs more" style="top:3017px"><b>+</b>View More Options</p>
  <div class="abs cards" style="top:3063px">
    <article class="card"><div class="photo" role="img" aria-label="Living room with sofa and indoor plant" style="background:linear-gradient(135deg,#efece6,#cbbfae 55%,#7f8a62)"></div><span class="badge">Sold</span><span class="price">$369,900+</span><h3>Ferndale Park</h3><p class="addr"><svg width="14" height="14"><use href="#i-pin"/></svg>52/144 Parkview Road Linden</p><div class="feats"><span><svg width="22" height="16"><use href="#i-bed"/></svg>1</span><span><svg width="22" height="16"><use href="#i-bath"/></svg>1</span><span><svg width="24" height="16"><use href="#i-car"/></svg>1</span></div><div class="agent"><span class="avatar"></span>Mei Lin<span class="tools"><svg width="16" height="16"><use href="#i-clock"/></svg><svg width="16" height="16"><use href="#i-expand"/></svg><svg width="16" height="16"><use href="#i-mail"/></svg></span></div></article>
    <article class="card"><div class="photo" role="img" aria-label="City apartment towers" style="background:linear-gradient(180deg,#9fbde0,#8f949a 55%,#4a4f55)"></div><span class="badge">Sold</span><span class="price">$369,900+</span><h3>Ferndale Park</h3><p class="addr"><svg width="14" height="14"><use href="#i-pin"/></svg>130/264 Market Walk Central</p><div class="feats"><span><svg width="22" height="16"><use href="#i-bed"/></svg>1</span><span><svg width="22" height="16"><use href="#i-bath"/></svg>1</span><span><svg width="24" height="16"><use href="#i-car"/></svg>1</span></div><div class="agent"><span class="avatar"></span>Mei Lin<span class="tools"><svg width="16" height="16"><use href="#i-clock"/></svg><svg width="16" height="16"><use href="#i-expand"/></svg><svg width="16" height="16"><use href="#i-mail"/></svg></span></div></article>
    <article class="card"><div class="photo" role="img" aria-label="Apartment block under blue sky" style="background:linear-gradient(180deg,#5a8fd4,#d8d6cf 55%,#7a8b5a)"></div><span class="badge">Sold</span><span class="price">$369,900+</span><h3>Ferndale Park</h3><p class="addr"><svg width="14" height="14"><use href="#i-pin"/></svg>407/1 Juniper Street Rowan</p><div class="feats"><span><svg width="22" height="16"><use href="#i-bed"/></svg>1</span><span><svg width="22" height="16"><use href="#i-bath"/></svg>1</span><span><svg width="24" height="16"><use href="#i-car"/></svg>1</span></div><div class="agent"><span class="avatar"></span>Mei Lin<span class="tools"><svg width="16" height="16"><use href="#i-clock"/></svg><svg width="16" height="16"><use href="#i-expand"/></svg><svg width="16" height="16"><use href="#i-mail"/></svg></span></div></article>
    <article class="card"><div class="photo" role="img" aria-label="Brick house with garage" style="background:linear-gradient(180deg,#4a7cc4,#6b4a3a 55%,#3a3330)"></div><span class="badge">Sold</span><span class="price">$369,900+</span><h3>Ferndale Park</h3><p class="addr"><svg width="14" height="14"><use href="#i-pin"/></svg>7 Heron Street Brookfield</p><div class="feats"><span><svg width="22" height="16"><use href="#i-bed"/></svg>1</span><span><svg width="22" height="16"><use href="#i-bath"/></svg>1</span><span><svg width="24" height="16"><use href="#i-car"/></svg>1</span></div><div class="agent"><span class="avatar"></span>Mei Lin<span class="tools"><svg width="16" height="16"><use href="#i-clock"/></svg><svg width="16" height="16"><use href="#i-expand"/></svg><svg width="16" height="16"><use href="#i-mail"/></svg></span></div></article>
    <article class="card"><div class="photo" role="img" aria-label="Modern apartment building" style="background:linear-gradient(180deg,#b7cbe0,#55606a 55%,#2e353b)"></div><span class="badge">Sold</span><span class="price">$369,900+</span><h3>Ferndale Park</h3><p class="addr"><svg width="14" height="14"><use href="#i-pin"/></svg>711/1 Quarry Street Northgate</p><div class="feats"><span><svg width="22" height="16"><use href="#i-bed"/></svg>1</span><span><svg width="22" height="16"><use href="#i-bath"/></svg>1</span><span><svg width="24" height="16"><use href="#i-car"/></svg>1</span></div><div class="agent"><span class="avatar"></span>Mei Lin<span class="tools"><svg width="16" height="16"><use href="#i-clock"/></svg><svg width="16" height="16"><use href="#i-expand"/></svg><svg width="16" height="16"><use href="#i-mail"/></svg></span></div></article>
    <article class="card"><div class="photo" role="img" aria-label="Brick home with pergola and lawn" style="background:linear-gradient(180deg,#dfe6ee,#9a7458 50%,#4f7d3a)"></div><span class="badge">Sold</span><h3>Ferndale Park</h3><p class="addr"><svg width="14" height="14"><use href="#i-pin"/></svg>23 Willow Crescent Brookfield</p><div class="feats"><span><svg width="22" height="16"><use href="#i-bed"/></svg>1</span><span><svg width="22" height="16"><use href="#i-bath"/></svg>1</span><span><svg width="24" height="16"><use href="#i-car"/></svg>1</span></div><div class="agent"><span class="avatar"></span>Mei Lin<span class="tools"><svg width="16" height="16"><use href="#i-clock"/></svg><svg width="16" height="16"><use href="#i-expand"/></svg><svg width="16" height="16"><use href="#i-mail"/></svg></span></div></article>
  </div>
  <div class="abs pager" style="top:3913px">
    <span class="dark"><svg width="10" height="14" viewBox="0 0 10 14"><path d="M7 2 2 7l5 5" fill="none" stroke="#fff" stroke-width="1.6"/></svg></span><span>1</span><span class="on">2</span><span>3</span><span class="dark"><svg width="10" height="14" viewBox="0 0 10 14"><path d="M3 2l5 5-5 5" fill="none" stroke="#fff" stroke-width="1.6"/></svg></span>
  </div>
</section>

<footer class="abs footer">
  <div class="abs f-brand"><span class="brand-mark"></span><span class="brand-name">Ferndale Estate</span></div>
  <p class="abs f-about">Lorem ipsum dolor sit amet, consectetur adipiscing elit, sed do eiusmod tempor...</p>
  <div class="abs f-col" style="left:332px">
    <h4>Site Map</h4>
    <ul><li>Home</li><li>About Us</li><li>Landload</li><li>Tenant</li><li>Make a Switch</li><li>Property Sales</li><li>Appraisal now</li></ul>
  </div>
  <div class="abs f-col" style="left:613px">
    <h4>Contact Us</h4>
    <div class="contact-row"><svg width="18" height="18"><use href="#i-pin"/></svg><span>18/4 Wattle Grove Rd,<br>Ferndale Park, ACT, 2990</span></div>
    <div class="contact-row"><svg width="18" height="18" viewBox="0 0 18 18"><path d="M4 2h3l1.5 4-2 1.5a9 9 0 0 0 4 4l1.5-2 4 1.5v3a2 2 0 0 1-2 2A14 14 0 0 1 2 4a2 2 0 0 1 2-2z" fill="none" stroke="#555" stroke-width="1.3"/></svg><b style="font-weight:500">02 6100 2381<br>02 6100 7745</b></div>
    <div class="contact-row"><svg width="18" height="18"><use href="#i-mail"/></svg><span>info@ferndaleestate.com</span></div>
  </div>
  <div class="abs f-col" style="left:889px">
    <h4>Social Media</h4>
    <div class="socials"><span class="filled"></span><span></span><span></span><span></span></div>
  </div>
</footer>
<div class="abs f-bottom">
  <span>2022© Ferndale Estate Properties. All right reserved.</span>
  <nav><span>Privacy</span><span>Complaint Handling &amp; Dispute Resolution</span><span>Due Diligence Checklist</span></nav>
</div>
</body>
</html>
```